Thank You Card Design for Personal Injury Law Firm

Hi -
I am interested in getting a design for a thank you card that captures my law firm's brand. I am providing a drop box link to a folder that contains pictures of the firm's staff and some happy clients. The dropbox folder will also include a folder that we mail to prospective clients. You may want to use pictures from it in addition to or in place of staff and client pictures. https://www.filquorra.net/sh/pelv3kx7tumwq2b/ZTRNLbcHoWEqJFm42tixpRk8y?dl=0

Target Market(s)

Adult males and females who have been in car accidents

Industry/Entity Type

Legal

Requirements
Nice to have
• Want it to have a happy, cheerful feel. But it must also be professional.

```html
<!DOCTYPE html>
<html lang="en">
<head>
<meta charset="UTF-8">
<title>Harlow Law Group – Thank You Card</title>
<link href="https://fonts.googleapis.com/css2?family=Montserrat:wght@500;600;700&display=swap" rel="stylesheet">
<style>
  :root{
    --brand-blue:#1d5a8e;
    --brand-navy:#17476f;
    --frame-line:#2f6a9c;
    --card-white:#ffffff;
    --page-bg:#e8ebee;
    --text-dark:#1d4f7c;
  }
  *{box-sizing:border-box;margin:0;padding:0}
  html,body{width:1200px;height:800px;overflow:hidden}
  body{
    background:var(--page-bg);
    font-family:"Montserrat",Arial,sans-serif;
    display:flex;align-items:center;justify-content:center;
  }
  .thank-you-card{
    width:1110px;height:740px;background:var(--card-white);
    box-shadow:0 6px 22px rgba(0,0,0,.12);
    padding:30px;
  }
  .card-frame{
    width:100%;height:100%;
    border:1.5px solid var(--frame-line);
    display:grid;grid-template-rows:172px 1fr 200px;grid-template-columns:100%;
    overflow:hidden;
  }
  .photo-strip{
    display:flex;justify-content:space-between;align-items:center;
    padding:0 34px;min-width:0;
  }
  .photo-strip--top{border-bottom:1.5px solid var(--frame-line)}
  .photo-strip--bottom{border-top:1.5px solid var(--frame-line)}
  .photo-group{display:flex}
  .photo{height:112px;display:block;flex:none}
  .photo--top-left{width:116px}
  .photo--top-right{width:130px}
  .photo--bottom{width:112px}
  .photo--office{background:linear-gradient(135deg,#e9dcc6,#2f4f86 65%,#3a4a6a)}
  .photo--suits{background:linear-gradient(160deg,#c9d3da,#5874a4 55%,#2b3e6a)}
  .photo--sign{background:linear-gradient(150deg,#e7ebef,#aab6c2 60%,#6b87a6)}
  .photo--portrait{background:linear-gradient(170deg,#f1ebe6,#e9c9b2 55%,#d7b8a6)}
  .photo--family{background:linear-gradient(150deg,#3f5f8c,#2aa0d6 55%,#d9b59d)}
  .photo--desk{background:linear-gradient(160deg,#7a3a33,#e9e5df 50%,#2a2a30)}
  .photo--pair{background:linear-gradient(150deg,#eef0ea,#7f8fa0 50%,#4d6b3e)}
  .photo--smile{background:linear-gradient(160deg,#efe6e0,#c1554e 55%,#6a3e3e)}
  .photo--seated{background:linear-gradient(160deg,#d8d6d3,#27355c 55%,#9b7f72)}
  .photo--garden{background:linear-gradient(160deg,#8eb870,#5a7a4a 50%,#8a7060)}
  .photo--handshake{background:linear-gradient(160deg,#9fc08a,#3f7bb6 55%,#505a68)}
  .photo--client{background:linear-gradient(160deg,#c8d2dc,#6a4a3a 50%,#eceae6)}
  .photo--walk{background:linear-gradient(160deg,#a9c98c,#2d2d36 55%,#8aa0b6)}

  .card-body{display:flex;align-items:center;padding:0 90px 0 64px;min-width:0}
  .firm-details{flex:1;display:flex;flex-direction:column;align-items:flex-start}
  .firm-name{
    display:flex;align-items:center;gap:16px;
    color:var(--brand-navy);font-weight:500;font-size:32px;
    letter-spacing:.5px;line-height:1.1;margin-bottom:30px;
  }
  .firm-name__mark{width:76px;height:76px;background:var(--brand-navy);flex:none}
  .firm-contact{margin-left:70px;text-align:center;color:var(--text-dark)}
  .firm-contact__phone{font-weight:700;font-size:28px;letter-spacing:.5px;margin-bottom:8px}
  .firm-contact__address{font-weight:600;font-size:15px;margin-bottom:6px}
  .firm-contact__web{font-weight:600;font-size:15px}
  .thank-you{
    color:var(--brand-blue);font-weight:700;font-size:80px;
    line-height:1.05;text-align:center;margin-top:-40px;
  }
</style>
</head>
<body>
  <main class="thank-you-card">
    <div class="card-frame">
      <section class="photo-strip photo-strip--top">
        <div class="photo-group">
          <div class="photo photo--top-left photo--office" role="img" aria-label="Attorney in suit seated at office desk"></div>
          <div class="photo photo--top-left photo--suits" role="img" aria-label="Two attorneys in suits standing outside"></div>
          <div class="photo photo--top-left photo--sign" role="img" aria-label="Firm sign outside the office building"></div>
          <div class="photo photo--top-left photo--portrait" role="img" aria-label="Smiling staff member portrait"></div>
        </div>
        <div class="photo-group">
          <div class="photo photo--top-right photo--family" role="img" aria-label="Happy client family with a baby"></div>
          <div class="photo photo--top-right photo--desk" role="img" aria-label="Attorney in vest seated at desk"></div>
          <div class="photo photo--top-right photo--pair" role="img" aria-label="Two staff members standing together outdoors"></div>
        </div>
      </section>

      <section class="card-body">
        <div class="firm-details">
          <div class="firm-name"><span class="firm-name__mark"></span><span>Harlow<br>Law Group</span></div>
          <div class="firm-contact">
            <p class="firm-contact__phone">907 555 0142</p>
            <p class="firm-contact__address">418 Birch Street • Fairview, AK 99502</p>
            <p class="firm-contact__web">www.harlowlawgroup.com</p>
          </div>
        </div>
        <h1 class="thank-you">Thank<br>You</h1>
      </section>

      <section class="photo-strip photo-strip--bottom">
        <div class="photo-group">
          <div class="photo photo--bottom photo--smile" role="img" aria-label="Smiling staff member at the office"></div>
          <div class="photo photo--bottom photo--seated" role="img" aria-label="Staff member seated with hands folded"></div>
          <div class="photo photo--bottom photo--garden" role="img" aria-label="Staff member outdoors among greenery"></div>
        </div>
        <div class="photo-group">
          <div class="photo photo--bottom photo--handshake" role="img" aria-label="Attorney shaking hands with a client outdoors"></div>
          <div class="photo photo--bottom photo--client" role="img" aria-label="Happy client leaning on a railing"></div>
          <div class="photo photo--bottom photo--walk" role="img" aria-label="Client couple walking outdoors"></div>
        </div>
      </section>
    </div>
  </main>
</body>
</html>
```